Business cards for Harbourline Supply Pty Ltd that import building products into Australia from China
Target Market(s)
Business to Business
Industry/Entity Type
Business
Contact Information for Business Card
Front: Logo and Business Name
Rear:
Desmond Varrick
General Manager
Mobile: 0427 561 394
email: dessie@harbourlinesupply.com.au
alternative email: dessie@outbackworks.com.au
web: www.harbourlinesupply.com.au
Adelaide, Brisbane and Darwin
Colors
ec1f27
fbee3d

```html
<!DOCTYPE html>
<html lang="en">
<head>
<meta charset="utf-8">
<title>Outback Works – Business Cards</title>
<link rel="stylesheet" href="https://fonts.googleapis.com/css2?family=Open+Sans:wght@400;600;700;800&display=swap">
<style>
  :root {
    --orange: #f39220;
    --charcoal: #2b2b2b;
    --ink: #222222;
    --paper: #ffffff;
    --backdrop: #e4e5e7;
    --rule: #555555;
  }
  * { box-sizing: border-box; margin: 0; padding: 0; }
  html, body { width: 1200px; height: 977px; overflow: hidden; }
  body {
    background: var(--backdrop);
    font-family: "Open Sans", Arial, sans-serif;
    position: relative;
  }
  .card {
    position: absolute;
    left: 270px;
    width: 660px;
    height: 377px;
    box-shadow: 0 8px 24px rgba(0,0,0,.18);
    overflow: hidden;
  }
  .card--front { top: 70px; background: var(--orange); }
  .card--rear { top: 530px; background: var(--paper); }

  /* Front */
  .front-brand {
    position: absolute; left: 150px; top: 125px;
    display: flex; align-items: center; gap: 22px;
  }
  .brand-square { width: 92px; height: 92px; background: var(--paper); }
  .brand-name {
    font-weight: 800; font-size: 44px; letter-spacing: 1px;
    color: var(--paper); line-height: 1;
  }
  .front-locations {
    position: absolute; left: 0; right: 0; top: 300px;
    text-align: center; color: var(--paper);
    font-size: 14px; font-weight: 600; letter-spacing: 1.5px;
  }
  .front-locations .sep { margin: 0 14px; }

  /* Rear */
  .rear-brand {
    position: absolute; left: 58px; top: 52px;
    display: flex; align-items: center; gap: 16px;
  }
  .rear-brand .brand-square { width: 66px; height: 66px; background: var(--orange); }
  .rear-brand .brand-name { font-size: 32px; color: var(--charcoal); }
  .rear-divider {
    position: absolute; left: 132px; top: 200px; width: 490px;
    height: 1px; background: var(--rule);
  }
  .person { position: absolute; left: 120px; top: 150px; }
  .person-name { font-size: 22px; font-weight: 600; color: var(--ink); }
  .person-title { font-size: 13px; font-weight: 600; color: var(--ink); margin-top: 2px; }
  .contacts {
    position: absolute; left: 140px; top: 214px;
    list-style: none; font-size: 13px; color: var(--ink);
  }
  .contacts--right { left: 390px; top: 150px; }
  .contacts li { display: flex; align-items: center; gap: 10px; height: 24px; }
  .contacts svg { width: 14px; height: 14px; fill: var(--orange); flex: none; }
  .rear-band { position: absolute; left: 0; bottom: 0; width: 660px; height: 70px; }
</style>
</head>
<body>

<section class="card card--front" aria-label="Business card front">
  <div class="front-brand">
    <div class="brand-square"></div>
    <div class="brand-name">OUTBACK WORKS</div>
  </div>
  <p class="front-locations">ADELAIDE<span class="sep">|</span>BRISBANE<span class="sep">|</span>DARWIN</p>
</section>

<section class="card card--rear" aria-label="Business card rear">
  <div class="rear-brand">
    <div class="brand-square"></div>
    <div class="brand-name">OUTBACK WORKS</div>
  </div>

  <div class="person">
    <p class="person-name">Desmond Varrick</p>
    <p class="person-title">General Manager</p>
  </div>
  <div class="rear-divider"></div>

  <ul class="contacts">
    <li>
      <svg viewBox="0 0 24 24"><path d="M6.6 10.8a15 15 0 0 0 6.6 6.6l2.2-2.2a1 1 0 0 1 1-.25 11.4 11.4 0 0 0 3.6.57 1 1 0 0 1 1 1V20a1 1 0 0 1-1 1A17 17 0 0 1 3 4a1 1 0 0 1 1-1h3.5a1 1 0 0 1 1 1c0 1.25.2 2.45.57 3.57a1 1 0 0 1-.25 1z"/></svg>
      0427 561 394
    </li>
    <li>
      <svg viewBox="0 0 24 24"><path d="M2 5h20v14H2z M2 5l10 8 10-8" fill="none" stroke="#f39220" stroke-width="2"/><path d="M2 6l10 7 10-7v13H2z"/></svg>
      dessie@harbourlinesupply.com.au
    </li>
  </ul>

  <ul class="contacts contacts--right">
    <li>
      <svg viewBox="0 0 24 24"><path d="M2 6l10 7 10-7v13H2z"/><path d="M2 5h20l-10 7z"/></svg>
      dessie@outbackworks.com.au
    </li>
    <li>
      <svg viewBox="0 0 24 24"><circle cx="12" cy="12" r="9" fill="none" stroke="#f39220" stroke-width="2"/><path d="M3 12h18M12 3c3 3 3 15 0 18M12 3c-3 3-3 15 0 18" fill="none" stroke="#f39220" stroke-width="1.5"/></svg>
      www.harbourlinesupply.com.au
    </li>
  </ul>

  <svg class="rear-band" viewBox="0 0 660 70" aria-hidden="true">
    <polygon points="0,46 540,6 528,70 0,70" fill="#f39220"/>
    <polygon points="552,5 660,0 660,70 540,70" fill="#2b2b2b"/>
  </svg>
</section>

</body>
</html>
```